Membership Drive "CHRISTMAS SPECIAL"

Looking to run a "Christmas Special" on 6 month Memberships for December 2019 to boost membership number up. This is a great time to get people exercising and everyone loves a Christmas Sale. Special is designed to attract more people to join and enjoy the savings.
Artwork will be display via social media (FP and Pictora) as well as in store. Artwork must be eye catching and direct to the customer. Customer should feel a sense of relief with being able to exercise at a lower cost .

Heading: "Christmas Sale"
6 Months
$199.00 Save over 30%
Terms and conditions apply"
*Offer End 31st December

below are other promos we had designed on Sketch Harbor along with potential photos to be included into this promo

Target Market(s)

Males and Females aged between 16 - 45

Industry/Entity Type

Fitness

Colors

Designer to choose colors to be used in the design.

Requirements
Must have
• Must emphasize "Christmas Special" $199.00 Save over 30%
• Terms and conditions apply
• Offer Ends 31st of December
• "All of our contact details"
• Address: 14 Marlow Rd Fernhill 3187
• Ph: 9428 7160
• www.stridelane.com.au
• Design format must come in PDF for a AO poster and an Pictora format please
Nice to have
• Some Christmas feels to the artwork

```html
<!DOCTYPE html>
<html lang="en">
<head>
<meta charset="utf-8">
<title>Super Christmas Special – Stride Lane Gymnasium</title>
<link rel="stylesheet" href="https://fonts.googleapis.com/css2?family=Great+Vibes&family=Poppins:wght@200;300;500;600;700&display=swap">
<style>
  :root {
    --festive-red: #d31a25;
    --red-glow: #f0342e;
    --pine-dark: #2f8a5a;
    --pine-light: #6fc25a;
    --ink: #0b0b0b;
    --paper: #ffffff;
  }
  * { margin: 0; padding: 0; box-sizing: border-box; }
  html, body { width: 849px; height: 1200px; overflow: hidden; background: var(--festive-red); }
  .poster {
    position: relative; width: 849px; height: 1200px; overflow: hidden;
    background: var(--festive-red);
    font-family: "Poppins", sans-serif;
  }
  .athlete-photo {
    position: absolute; left: 183px; top: 225px; width: 666px; height: 770px;
    background: radial-gradient(ellipse at 65% 50%, var(--red-glow) 0%, rgba(240,52,46,0.55) 45%, rgba(211,26,37,0) 75%);
  }
  .garland { position: absolute; left: 0; width: 849px; }
  .garland--top {
    top: 0; height: 280px;
    background: linear-gradient(180deg, var(--pine-dark) 0%, var(--pine-light) 55%, rgba(111,194,90,0.6) 80%, rgba(211,26,37,0) 100%);
  }
  .garland--bottom {
    bottom: 0; height: 250px;
    background: linear-gradient(0deg, var(--pine-dark) 0%, var(--pine-light) 60%, rgba(111,194,90,0.6) 82%, rgba(211,26,37,0) 100%);
  }
  .abs { position: absolute; left: 0; width: 849px; text-align: center; white-space: nowrap; }
  .intro { top: 253px; font-weight: 200; font-size: 31px; line-height: 41px; color: var(--ink); left: 8px; }
  .title-script { top: 345px; left: 4px; font-family: "Great Vibes", cursive; font-size: 150px; line-height: 150px; color: var(--paper); }
  .title-main { top: 467px; left: 0; font-weight: 700; font-size: 110px; line-height: 110px; color: var(--ink); letter-spacing: -1px; }
  .title-sub { top: 563px; left: -11px; font-weight: 200; font-size: 88px; line-height: 88px; color: var(--paper); }
  .discount-band { position: absolute; left: 175px; top: 675px; width: 475px; height: 87px; }
  .discount-text { top: 676px; left: 4px; font-weight: 700; font-size: 78px; line-height: 84px; color: var(--ink); }
  .deadline { top: 770px; left: 447px; width: 172px; text-align: right; font-weight: 500; font-size: 11.5px; line-height: 16px; color: var(--ink); }
  .price { top: 815px; left: 0; font-weight: 700; font-size: 66px; line-height: 72px; color: var(--paper); }
  .saving { top: 889px; font-weight: 600; font-size: 32px; line-height: 36px; color: var(--paper); }
  .term { top: 925px; font-weight: 600; font-size: 17px; line-height: 20px; color: var(--paper); }
  .brand { position: absolute; left: 15px; top: 1080px; display: flex; align-items: center; gap: 7px; }
  .brand-square { width: 14px; height: 14px; background: var(--ink); }
  .brand-name { font-weight: 700; font-size: 26px; line-height: 30px; color: var(--ink); letter-spacing: 0.5px; }
  .contact { position: absolute; left: 18px; font-weight: 500; color: var(--paper); font-variant: small-caps; font-size: 11.5px; line-height: 14px; }
  .contact--address { top: 1139px; }
  .contact--phone { top: 1159px; }
  .contact--web { top: 1177px; font-variant: normal; font-size: 9.5px; text-transform: uppercase; }
  .terms { position: absolute; right: 17px; top: 1175px; font-weight: 500; font-size: 11px; line-height: 14px; color: var(--paper); font-variant: small-caps; }
</style>
</head>
<body>
  <main class="poster">
    <div class="athlete-photo" role="img" aria-label="Muscular athlete stretching, photo toned in red"></div>
    <div class="garland garland--top" role="img" aria-label="Pine branch garland along the top edge"></div>
    <div class="garland garland--bottom" role="img" aria-label="Pine branch garland along the bottom edge"></div>

    <p class="abs intro">Start your new year resolution with<br>our Christmas off</p>
    <h1>
      <span class="abs title-script">Super</span>
      <span class="abs title-main">CHRISTMAS</span>
      <span class="abs title-sub">SPECIAL</span>
    </h1>

    <svg class="discount-band" viewBox="0 0 475 87" aria-hidden="true">
      <polygon points="21,0 475,0 450,87 0,87" fill="#ffffff"/>
    </svg>
    <p class="abs discount-text">30%OFF*</p>
    <p class="abs deadline">Offer Ends 31st of December</p>

    <p class="abs price">$199.00</p>
    <p class="abs saving">SAVE OVER 30%</p>
    <p class="abs term">WITH 6 MONTHS SUBSCRIPTION</p>

    <div class="brand"><span class="brand-square"></span><span class="brand-name">STRIDE LANE</span></div>
    <p class="contact contact--address">Address: 14 Marlow Rd Fernhill 3187</p>
    <p class="contact contact--phone">Ph: 9428 7160</p>
    <p class="contact contact--web">www.stridelane.com.au</p>
    <p class="terms">*Terms and conditions apply</p>
  </main>
</body>
</html>
```